Flat bootstrap design for existing site

I'm looking for a modern flat design based around an existing logo. This has to be a custom design (no external templates), and implemented into a bootstrap framework.

The logo is attached as 2 versions - choose whichever you want, that flows better with whatever design you choose.

Added screenshots of the existing site (currently using the default bootstrap layouts). Please make your designs around those pages in the screenshots (i.e. the homepage only has the postal code input and the header). The active page has 3 screenshots, because I wanted to illustrate the other states that would be visible (in the table rows).

This is a moving/junk removal website, just for some context.

Here's some example websites (flat designs) that I like, just to give you an idea of what I'm after.

https://www.plimvora.com/
https://dacklow.com/
https://trevanu.com/
https://quobrintal.com/en/

Coding

Coded - Design and coding required

Number of Pages Required

5+ page

Colors

Designer to choose colors to be used in the design.

Requirements
Must have
• It must be a modern/simple flat design, that is built around the existing logo (attached).
• It has to be implemented using bootstrap.

```html
<!DOCTYPE html>
<html lang="en">
<head>
<meta charset="utf-8">
<title>Haulbrook — Junk Removal</title>
<link rel="stylesheet" href="https://fonts.googleapis.com/css2?family=Open+Sans:wght@400;600;700&display=swap">
<style>
  :root {
    --brand: #48c7f5;
    --brand-deep: #2eb0e0;
    --white: #ffffff;
    --ink: #4a4a4a;
    --muted: #8a8a8a;
    --placeholder: #777777;
    --hero-dark: #2e2620;
    --hero-mid: #6b5440;
    --hero-blue: #1f5f86;
  }
  * { box-sizing: border-box; margin: 0; padding: 0; }
  html, body {
    width: 1200px;
    height: 614px;
    overflow: hidden;
    font-family: "Open Sans", Arial, sans-serif;
    background: var(--white);
  }
  .site-header {
    position: absolute;
    top: 0; left: 0;
    width: 1200px; height: 80px;
    background: var(--brand);
  }
  .brand {
    position: absolute;
    left: 132px; top: 0;
    height: 80px;
    display: flex; align-items: center; gap: 8px;
    color: var(--white);
    font-weight: 700;
    font-size: 26px;
    letter-spacing: 0.5px;
  }
  .brand-mark {
    width: 14px; height: 14px;
    border-radius: 50%;
    background: var(--white);
  }
  .main-nav {
    position: absolute;
    top: 19px; right: 0;
    height: 40px;
    display: flex; align-items: center;
  }
  .main-nav a {
    color: var(--white);
    text-decoration: none;
    font-size: 15px;
    line-height: 40px;
    padding: 0 16px;
  }
  .main-nav .nav-book { position: absolute; left: -540px; }
  .nav-link-book { position: absolute; left: 641px; }
  .nav-list { list-style: none; }
  .nav-item { position: absolute; top: 19px; height: 40px; line-height: 40px; color: var(--white); font-size: 15px; text-decoration: none; }
  .nav-item.book { left: 643px; }
  .nav-item.how { left: 725px; }
  .nav-item.driver {
    left: 848px; width: 144px;
    text-align: center;
    background: var(--brand-deep);
    border-radius: 3px;
  }
  .nav-item.signin { left: 1023px; }

  .hero {
    position: absolute;
    top: 80px; left: 0;
    width: 1200px; height: 480px;
  }
  .hero-photo {
    position: absolute; inset: 0;
    background:
      radial-gradient(ellipse 420px 260px at 920px 120px, rgba(31,95,134,0.85), rgba(31,95,134,0) 70%),
      radial-gradient(ellipse 300px 200px at 300px 420px, rgba(150,110,40,0.55), rgba(150,110,40,0) 70%),
      linear-gradient(160deg, var(--hero-mid) 0%, var(--hero-dark) 55%, #3a3028 100%);
  }
  .hero-shade {
    position: absolute; inset: 0;
    background: rgba(0,0,0,0.25);
  }
  .hero-title {
    position: absolute;
    top: 178px; left: 0; width: 1200px;
    text-align: center;
    color: var(--white);
    font-size: 42px;
    font-weight: 400;
    line-height: 56px;
    text-shadow: 0 2px 6px rgba(0,0,0,0.35);
  }
  .hero-title strong { font-weight: 700; }
  .booking-form {
    position: absolute;
    top: 245px; left: 400px;
    width: 400px; height: 48px;
    display: flex;
  }
  .postal-input {
    width: 320px; height: 48px;
    border: 0; outline: 0;
    padding: 0 22px;
    font-family: inherit;
    font-size: 13px;
    color: var(--ink);
    background: var(--white);
  }
  .postal-input::placeholder { color: var(--placeholder); }
  .book-button {
    width: 80px; height: 48px;
    border: 0;
    background: var(--brand);
    color: var(--white);
    font-family: inherit;
    font-weight: 600;
    font-size: 15px;
    letter-spacing: 0.5px;
  }
  .site-footer {
    position: absolute;
    top: 560px; left: 0;
    width: 1200px; height: 54px;
    text-align: center;
    font-size: 10.5px;
    line-height: 54px;
    color: var(--ink);
  }
</style>
</head>
<body>
  <header class="site-header">
    <div class="brand"><span class="brand-mark"></span>HAULBROOK</div>
    <nav>
      <a class="nav-item book" href="#">Book</a>
      <a class="nav-item how" href="#">How It Works</a>
      <a class="nav-item driver" href="#">Become a Driver</a>
      <a class="nav-item signin" href="#">Sign In</a>
    </nav>
  </header>

  <section class="hero">
    <div class="hero-photo" role="img" aria-label="Photo of cardboard boxes, bags and household items ready for junk removal"></div>
    <div class="hero-shade"></div>
    <h1 class="hero-title">Need junk removed? <strong>Book now</strong></h1>
    <form class="booking-form">
      <input class="postal-input" type="text" placeholder="Postal Code">
      <button class="book-button" type="button">BOOK</button>
    </form>
  </section>

  <footer class="site-footer">Copyright &copy; 2017 Haulbrook. All rights reserved.</footer>
</body>
</html>
```